Lorna Vale Industries Wix Site

Company website run as a hobby by my daughter Lorna. She wants to be able to offer multiple products for sale online (so etail enabled). Personalized products like bracelets and necklaces with people's names. Piggy Banks with kids names. Trail Keeper cookies when in season. Not childish in presentation but easy to navigate by kids. Big images like on original website (lornavalebakes.com). Same humor as on that site (go to the cart and empty it and you will get the idea. Colors Gold like on the bird in her attached card. Blue should be lighter than that card (robins egg type of blue). Avoid the green on the biz card. Basics of a new website with About Us, Contact, social media and a cart with payment options via coinrill. mobile version nice to have but not mandataory.

```html
<!DOCTYPE html>
<html lang="en">
<head>
<meta charset="utf-8">
<title>Lorna Vale – Bracelets, Necklaces and Piggy Banks</title>
<link rel="stylesheet" href="https://fonts.googleapis.com/css2?family=Oswald:wght@300;400;500&family=Open+Sans:wght@400;600&display=swap">
<style>
:root{
  --gold:#b5952f;
  --gold-dark:#9c7f22;
  --teal:#1bbbbd;
  --ink:#333333;
  --muted:#888888;
  --line:#e6e6e6;
  --price:#e8822d;
  --star:#f0a829;
  --footer:#2e2e2e;
  --footer-text:#b8b8b8;
  --page-top:#efefef;
}
*{box-sizing:border-box;margin:0;padding:0}
html,body{width:1200px;height:2182px;overflow:hidden}
body{
  position:relative;
  font-family:"Open Sans",Arial,sans-serif;
  color:var(--ink);
  background:linear-gradient(180deg,var(--page-top) 0,#f6f6f6 500px,#ffffff 640px,#ffffff 100%);
}
h1,h2,h3,h4{font-weight:inherit}
.wrap{position:absolute;left:172px;width:858px}
a{color:inherit;text-decoration:none}
.heading{font-family:"Oswald",sans-serif;font-weight:300;text-transform:uppercase;color:var(--ink)}

/* header */
.brand{position:absolute;left:172px;top:112px;font-family:"Open Sans",sans-serif;font-weight:600;font-size:22px;color:var(--ink);white-space:nowrap}
.top-links{position:absolute;right:170px;top:42px;display:flex;gap:34px;font-size:11px;color:#666}
.top-links span{display:flex;align-items:center;gap:8px}
.cart-box{position:absolute;left:855px;top:96px;width:175px;height:29px;border:1px solid #dcdcdc;background:#fff;display:flex;align-items:center;padding:0 10px;font-size:11px;color:#999;gap:7px}
.cart-box b{font-weight:400;color:var(--price)}
.cart-box strong{margin-left:auto;font-weight:400;font-size:14px;color:var(--ink)}

/* navigation */
.nav{top:164px;height:51px}
.category-btn{position:absolute;left:0;top:0;width:175px;height:51px;background:var(--gold);color:#fff;font-family:"Oswald",sans-serif;font-size:13px;letter-spacing:1px;display:flex;align-items:center;justify-content:space-between;padding:0 18px}
.main-nav{position:absolute;left:192px;top:0;width:666px;height:51px;background:var(--teal);display:flex;align-items:center;padding-left:10px}
.main-nav a{color:#fff;font-size:15px;padding:0 14px;border-right:1px solid rgba(255,255,255,.3);line-height:24px}
.main-nav a:last-child{border:none}

/* hero */
.hero{top:233px;height:484px;border-radius:4px;overflow:hidden}
.hero-photo{position:absolute;inset:0;background:radial-gradient(circle at 74% 45%,#7a5d4f 0,#3a2b26 22%,#121212 48%),linear-gradient(90deg,#2a2a2a,#0a0a0a)}
.hero-copy{position:absolute;left:69px;top:130px;color:#fff}
.hero-title{font-family:"Oswald",sans-serif;font-weight:500;font-size:54px;line-height:1}
.hero-sub{font-family:"Oswald",sans-serif;font-weight:500;font-size:38px;line-height:1.3;margin-top:10px}
.hero-text{font-size:14px;line-height:22px;width:390px;margin-top:14px}
.hero-arrows{display:flex;gap:8px;margin-top:28px}
.arrow-btn{width:24px;height:24px;border-radius:50%;background:rgba(255,255,255,.15);display:flex;align-items:center;justify-content:center}

/* best sellers */
.section-title{top:743px;font-size:21px}
.pager{position:absolute;right:170px;top:748px;display:flex;gap:4px}
.pager span{width:17px;height:17px;border:1px solid #ccc;border-radius:50%;background:#fff;display:flex;align-items:center;justify-content:center}
.products{top:796px;height:330px}
.product{position:absolute;top:0;width:195px}
.product-media{height:205px;border:1px solid var(--line);background:#fafafa;position:relative}
.product-media .stars{position:absolute;left:13px;top:12px}
.product-img{position:absolute;left:22px;top:40px;right:22px;bottom:22px;border-radius:50%;background:radial-gradient(circle,#e9c767 0,#d4a83a 40%,rgba(250,250,250,0) 70%)}
.product-info{margin-top:6px;height:78px;border:1px solid var(--line);background:#fff;text-align:center;padding-top:14px}
.product-name{font-family:"Oswald",sans-serif;font-weight:300;font-size:15px}
.product-price{font-family:"Oswald",sans-serif;font-weight:300;font-size:16px;margin-top:8px}
.product-price b{font-weight:300;color:var(--price);margin-left:4px}
.product-actions{margin-top:6px;height:33px;border:1px solid var(--line);background:#fff;display:flex;align-items:center;justify-content:center;gap:16px;font-size:11px;color:#777;text-transform:uppercase}
.product-actions span{display:flex;align-items:center;gap:6px}
.stars{color:var(--star);font-size:10px;letter-spacing:1px}
.stars i{font-style:normal;color:#ccc}

/* promos */
.promos{top:1169px;height:320px}
.promo{position:absolute;top:0;width:269px;text-align:center}
.promo-img{height:155px}
.promo-title{font-size:16px;margin-top:20px;font-weight:400}
.promo-text{font-size:11px;line-height:21px;color:#777;margin-top:8px;padding:0 14px}
.btn-gold{display:inline-block;margin-top:18px;background:var(--gold);color:#fff;font-family:"Oswald",sans-serif;font-size:13px;width:118px;height:32px;line-height:32px;border-radius:2px;box-shadow:0 2px 0 var(--gold-dark)}

/* features */
.features{top:1529px;height:141px}
.feature{position:absolute;top:0;width:270px;height:141px;background:#f7f7f7;border:1px solid #ececec;border-radius:3px;box-shadow:0 2px 0 #e2e2e2}
.feature-icon{position:absolute;left:20px;top:40px;width:60px;height:60px;display:flex;align-items:center;justify-content:center}
.feature-body{position:absolute;left:104px;top:20px;right:8px}
.feature-title{font-family:"Oswald",sans-serif;font-weight:400;font-size:15px;color:var(--teal);text-transform:uppercase;white-space:nowrap}
.feature-text{font-size:11px;line-height:19px;color:#888;margin-top:6px}
.feature-more{font-size:10px;color:var(--teal);margin-top:4px}

/* search */
.search{top:1705px;height:84px;background:#f4f4f4;border:1px solid #e4e4e4;border-radius:3px;z-index:2}
.search-input{position:absolute;left:24px;top:21px;width:636px;height:44px;background:#fff;border:1px solid #e6e6e6;border-radius:3px;font-size:13px;color:#999;padding:13px 16px}
.search-btn{position:absolute;left:673px;top:21px;width:159px;height:44px;background:var(--teal);color:#fff;border-radius:3px;font-size:15px;text-align:center;line-height:44px}

/* footer */
.footer{position:absolute;left:0;top:1754px;width:1200px;height:368px;background:var(--footer);color:var(--footer-text)}
.foot-col{position:absolute;top:80px}
.foot-title{font-family:"Oswald",sans-serif;font-weight:300;font-size:16px;color:#ddd;text-transform:uppercase;margin-bottom:18px}
.recent{display:flex;gap:12px;margin-bottom:20px}
.recent-thumb{width:58px;height:58px;background:radial-gradient(circle,#6a6a6a 0,#111 60%);border:1px solid #555}
.recent-name{font-size:14px;color:#ccc}
.recent-price{font-size:15px;color:#aaa;margin-top:6px}
.foot-links{list-style:none;font-size:11px;line-height:20.5px}
.contact-row{font-size:12px;line-height:20px;display:flex;gap:12px;margin-bottom:10px}
.social li{list-style:none;font-size:12px;line-height:28px;display:flex;align-items:center;gap:14px}
.social i{width:8px;height:8px;border-radius:50%;background:#999}
.foot-divider{position:absolute;left:172px;top:282px;width:858px;height:1px;background:#3d3d3d}
.newsletter{position:absolute;left:172px;top:310px;display:flex;gap:10px}
.email-input{width:185px;height:31px;background:#272727;border:1px solid #3a3a3a;font-size:10px;color:#777;padding:8px 12px}
.subscribe{height:31px;width:78px;background:var(--gold);color:#fff;font-size:12px;text-align:center;line-height:31px;border-radius:2px}
.share-dots{position:absolute;left:513px;top:316px;display:flex;gap:5px}
.share-dots span{width:21px;height:21px;border:1px solid #777;border-radius:50%}
.payments{position:absolute;left:671px;top:312px;display:flex;align-items:center;gap:10px}
.payments .label{font-family:"Oswald",sans-serif;font-weight:300;font-size:16px;color:#ccc;margin-right:32px}
.pay-card{width:46px;height:28px;border-radius:3px;background:#9b9b9b;color:#333;font-size:8px;font-weight:600;display:flex;align-items:center;justify-content:center}
.legal{position:absolute;left:0;top:2122px;width:1200px;height:60px;background:var(--gold);color:#fff;font-size:11px}
.legal .copy{position:absolute;left:177px;top:22px}
.legal .terms{position:absolute;left:862px;top:22px}
</style>
</head>
<body>

<header>
  <a class="brand" href="#">Lorna Vale</a>
  <nav class="top-links">
    <span><svg width="10" height="9" viewBox="0 0 10 9"><rect x="0" y="2" width="10" height="7" rx="1" fill="#666"/><rect x="3" y="0" width="4" height="3" fill="none" stroke="#666"/></svg>My Account</span>
    <span><svg width="10" height="9" viewBox="0 0 10 9"><path d="M5 9L1 5A2.3 2.3 0 0 1 5 2A2.3 2.3 0 0 1 9 5Z" fill="#666"/></svg>My Wishlist</span>
    <span><svg width="12" height="10" viewBox="0 0 12 10"><path d="M0 1h2l2 6h6l1.5-4.5H3" fill="none" stroke="#666"/><circle cx="5" cy="9" r="1" fill="#666"/><circle cx="9" cy="9" r="1" fill="#666"/></svg>CART (0)</span>
  </nav>
  <div class="cart-box">
    <svg width="14" height="12" viewBox="0 0 14 12"><path d="M1 4h12l-1.5 7h-9z M4 4l2-3 M10 4l-2-3" fill="none" stroke="#999"/></svg>
    Cart <b>0</b> items <strong>47,99 $</strong>
  </div>
</header>

<div class="wrap nav">
  <a class="category-btn" href="#">SHOP BY CATEGORY
    <svg width="10" height="8" viewBox="0 0 10 8"><path d="M1 1l4 3 4-3M1 4l4 3 4-3" fill="none" stroke="#fff" stroke-width="1.4"/></svg></a>
  <nav class="main-nav">
    <a href="#">Collections</a><a href="#">About us</a><a href="#">Shop</a><a href="#">Products</a><a href="#">Order Now</a><a href="#">Sign Up</a><a href="#">Contact us</a>
  </nav>
</div>

<section class="wrap hero">
  <div class="hero-photo" role="img" aria-label="Photo of a woman in profile wearing a tiara and long crystal earrings, photographer in the background"></div>
  <div class="hero-copy">
    <h1 class="hero-title">Lorna Vale</h1>
    <h2 class="hero-sub">Bracelets and Necklaces</h2>
    <p class="hero-text">Sed purus purus, tincidunt eget malesuada et, molestie ut eros. Fusce blandit, sapien eu sollicitudin consectetur,</p>
    <div class="hero-arrows">
      <span class="arrow-btn"><svg width="8" height="10" viewBox="0 0 8 10"><path d="M6 1L2 5l4 4" fill="none" stroke="#fff" stroke-width="1.5"/></svg></span>
      <span class="arrow-btn"><svg width="8" height="10" viewBox="0 0 8 10"><path d="M2 1l4 4-4 4" fill="none" stroke="#fff" stroke-width="1.5"/></svg></span>
    </div>
  </div>
</section>

<h2 class="wrap heading section-title">Best Sellers</h2>
<div class="pager">
  <span><svg width="6" height="8" viewBox="0 0 6 8"><path d="M5 1L2 4l3 3" fill="none" stroke="#777"/></svg></span>
  <span><svg width="6" height="8" viewBox="0 0 6 8"><path d="M1 1l3 3-3 3" fill="none" stroke="#777"/></svg></span>
</div>

<section class="wrap products">
  <article class="product" style="left:0">
    <div class="product-media"><span class="stars">★★★<i>★★</i></span><div class="product-img" role="img" aria-label="Gold chain bracelet with engraved tag"></div></div>
    <div class="product-info"><h3 class="product-name">Diamond Bracelet</h3><p class="product-price">$90.00<b>$100.00</b></p></div>
    <div class="product-actions"><span>♡ Wishlist</span><span>⇄ Compare</span></div>
  </article>
  <article class="product" style="left:221px">
    <div class="product-media"><span class="stars">★★★<i>★★</i></span><div class="product-img" role="img" aria-label="Gold necklace with script word pendant"></div></div>
    <div class="product-info"><h3 class="product-name">Jewelry Bracelets</h3><p class="product-price">$90.00<b>$100.00</b></p></div>
    <div class="product-actions"><span>♡ Wishlist</span><span>⇄ Compare</span></div>
  </article>
  <article class="product" style="left:442px">
    <div class="product-media"><span class="stars">★★★<i>★★</i></span><div class="product-img" role="img" aria-label="Gold bangle with crystal detail"></div></div>
    <div class="product-info"><h3 class="product-name">Best Platinum Necklaces</h3><p class="product-price">$90.00<b>$100.00</b></p></div>
    <div class="product-actions"><span>♡ Wishlist</span><span>⇄ Compare</span></div>
  </article>
  <article class="product" style="left:663px">
    <div class="product-media"><span class="stars">★★★<i>★★</i></span><div class="product-img" role="img" aria-label="Gold necklace with infinity pendant"></div></div>
    <div class="product-info"><h3 class="product-name">Willow Crest Necklaces</h3><p class="product-price">$90.00<b>$100.00</b></p></div>
    <div class="product-actions"><span>♡ Wishlist</span><span>⇄ Compare</span></div>
  </article>
</section>

<section class="wrap promos">
  <article class="promo" style="left:0">
    <div class="promo-img" role="img" aria-label="Heavy gold chain with gold plate on dark background" style="background:radial-gradient(circle at 45% 55%,#d8b545 0,#8a6d1e 30%,#2b2b2b 65%)"></div>
    <h3 class="heading promo-title">Check Our Bracelets</h3>
    <p class="promo-text">Lorem ipsum dolor sit amet, consectetur adipiscing elit, sed do eiusmod tempor Lorem ipsum dolor sit amet, consectetur</p>
    <a class="btn-gold" href="#">VISIT THE STORE</a>
  </article>
  <article class="promo" style="left:291px">
    <div class="promo-img" role="img" aria-label="Woman with jewellery against warm bokeh lights" style="background:linear-gradient(135deg,#8c7256 0,#3e3028 45%,#1e1a18 100%)"></div>
    <h3 class="heading promo-title">Summer Hat Collection</h3>
    <p class="promo-text">Lorem ipsum dolor sit amet, consectetur adipiscing elit, sed do eiusmod tempor Lorem ipsum dolor sit amet, consectetur</p>
    <a class="btn-gold" href="#">VISIT THE STORE</a>
  </article>
  <article class="promo" style="left:589px">
    <div class="promo-img" role="img" aria-label="Pink piggy bank with name lettering" style="background:radial-gradient(circle at 55% 60%,#f1b9b9 0,#d99a98 35%,#c9c2bd 75%)"></div>
    <h3 class="heading promo-title">Piggy Banks</h3>
    <p class="promo-text">Lorem ipsum dolor sit amet, consectetur adipiscing elit, sed do eiusmod tempor Lorem ipsum dolor sit amet, consectetur</p>
    <a class="btn-gold" href="#">VISIT THE STORE</a>
  </article>
</section>

<section class="wrap features">
  <article class="feature" style="left:0">
    <div class="feature-icon"><svg width="40" height="46" viewBox="0 0 40 46"><path d="M4 2l8 3 6 30h18" fill="none" stroke="#444" stroke-width="3"/><rect x="18" y="12" width="14" height="12" fill="none" stroke="#444" stroke-width="3" transform="rotate(-12 25 18)"/><circle cx="18" cy="40" r="4" fill="#444"/><circle cx="33" cy="40" r="4" fill="#444"/></svg></div>
    <div class="feature-body"><h3 class="feature-title">Very Fast Delivery.</h3><p class="feature-text">Lorem ipsum dolor sit amet, consectetur adipiscing elit. Sed viverra, urna quis</p><p class="feature-more">MORE →</p></div>
  </article>
  <article class="feature" style="left:294px">
    <div class="feature-icon"><svg width="50" height="50" viewBox="0 0 50 50"><path d="M12 18L25 5l13 13" fill="none" stroke="#444" stroke-width="2"/><circle cx="25" cy="5" r="3" fill="#444"/><rect x="3" y="18" width="44" height="28" rx="4" fill="#555"/><text x="25" y="37" text-anchor="middle" font-family="Open Sans,sans-serif" font-size="12" fill="#fff">SALE</text></svg></div>
    <div class="feature-body"><h3 class="feature-title">Every Week Discounts.</h3><p class="feature-text">Lorem ipsum dolor sit amet, consectetur adipiscing elit. Sed viverra, urna quis</p><p class="feature-more">MORE →</p></div>
  </article>
  <article class="feature" style="left:588px">
    <div class="feature-icon"><svg width="34" height="44" viewBox="0 0 34 44"><path d="M11 2h12l-4 8h-4z" fill="#444"/><path d="M14 10h6C30 16 34 26 32 34c-1 6-6 8-15 8S3 40 2 34C0 26 4 16 14 10z" fill="#444"/><text x="17" y="34" text-anchor="middle" font-family="Open Sans,sans-serif" font-weight="600" font-size="16" fill="#fff">$</text></svg></div>
    <div class="feature-body"><h3 class="feature-title">Money Saver.</h3><p class="feature-text">Lorem ipsum dolor sit amet, consectetur adipiscing elit. Sed viverra, urna quis</p><p class="feature-more">MORE →</p></div>
  </article>
</section>

<footer class="footer">
  <div class="foot-col" style="left:172px">
    <h4 class="foot-title">Recent Products</h4>
    <div class="recent"><div class="recent-thumb" role="img" aria-label="Silver necklace on black"></div><div><p class="recent-name">Sed ut perspiciatis</p><p class="stars">★★★<i>★★</i></p><p class="recent-price">$25.00</p></div></div>
    <div class="recent"><div class="recent-thumb" role="img" aria-label="Silver collar necklace on black"></div><div><p class="recent-name">Sed ut perspiciatis</p><p class="stars">★★★<i>★★</i></p><p class="recent-price">$25.00</p></div></div>
  </div>
  <div class="foot-col" style="left:454px">
    <h4 class="foot-title">My Account</h4>
    <ul class="foot-links"><li>My Rewards</li><li>Register</li><li>About Rewards</li><li>Shipping &amp; Returns</li><li>Privacy Notice</li><li>Sign In</li></ul>
  </div>
  <div class="foot-col" style="left:640px">
    <h4 class="foot-title">Contact Us</h4>
    <p class="contact-row" style="margin-bottom:18px">48120 Marlow Road ,<br>PO Box 2400, Ashgrove</p>
    <p class="contact-row"><svg width="16" height="16" viewBox="0 0 16 16"><path d="M3 1l3 3-2 2c1 2 3 4 6 6l2-2 3 3-2 2C7 15 1 9 1 3z" fill="none" stroke="#aaa"/></svg>1-800-555-0142</p>
    <p class="contact-row"><svg width="16" height="12" viewBox="0 0 16 12"><rect x=".5" y=".5" width="15" height="11" fill="none" stroke="#aaa"/><path d="M1 1l7 6 7-6" fill="none" stroke="#aaa"/></svg>info@lornavalebakes.com</p>
  </div>
  <div class="foot-col" style="left:940px">
    <h4 class="foot-title">Social Media</h4>
    <ul class="social"><li><i></i>Friendwall</li><li><i></i>Chirpline</li><li><i></i>Circlehub</li><li><i></i>Reelcast</li></ul>
  </div>
  <div class="foot-divider"></div>
  <form class="newsletter"><div class="email-input">Enter Your Email</div><div class="subscribe">subscribe</div></form>
  <div class="share-dots"><span></span><span></span><span></span></div>
  <div class="payments"><span class="label">Payments</span>
    <span class="pay-card">Coinrill</span><span class="pay-card">Cardora</span><span class="pay-card">Directa</span><span class="pay-card">Mintpay</span><span class="pay-card">Linkcard</span>
  </div>
</footer>

<div class="wrap search">
  <div class="search-input">Looking for another product? Use this search form and hit enter...</div>
  <div class="search-btn">Search Product</div>
</div>

<div class="legal">
  <span class="copy">©2013 - 2014 Lorna Vale, All Rights Reserved.</span>
  <span class="terms">Terms of Service | Privacy Policy</span>
</div>

</body>
</html>
```